Business Card Design for company

We want new business cards. We'd like something different-- yet still highly professional. Our tagline is Providing leadership, delivering success. Stock photos are ok, as long as they are relevant and look upscale.

Target Market(s)

Architecture/Business Management Consulting/Engineering Consulting

Contact Information for Business Card

dark gray background with pops of blue might be good, but you tell me. You're the designers. Rounded corners might be nice, but again, you tell me.

Font styles to use
Serif
Sans Serif

Colors
3276b5
5c5c5c
9d9d9d
fbfbfb

Requirements
Nice to have
• Something different, but still very professional.

```html
<!DOCTYPE html>
<html lang="en">
<head>
<meta charset="utf-8">
<title>Norvale International – Business Card</title>
<link rel="stylesheet" href="https://fonts.googleapis.com/css2?family=Montserrat:wght@600;700&family=Roboto:wght@400;500&display=swap">
<style>
  :root {
    --blue: #2a5f96;
    --blue-bright: #3276b5;
    --charcoal: #4a4e55;
    --grey-text: #5c5c5c;
    --grey-soft: #9d9d9d;
    --paper: #fbfbfb;
    --backdrop: #e6e4e1;
  }
  * { box-sizing: border-box; margin: 0; padding: 0; }
  html, body { width: 1200px; height: 1108px; overflow: hidden; }
  body {
    background: var(--backdrop);
    font-family: "Roboto", Arial, sans-serif;
    position: relative;
  }
  .card {
    position: absolute;
    left: 250px;
    width: 700px;
    height: 400px;
    border-radius: 6px;
    box-shadow: 0 10px 30px rgba(0,0,0,0.18);
    overflow: hidden;
  }
  /* Back side */
  .card--back { top: 90px; background: var(--charcoal); }
  .back__brand {
    position: absolute; left: 0; right: 0; top: 140px;
    text-align: center;
    font-family: "Montserrat", Arial, sans-serif;
    font-weight: 700; font-size: 72px; letter-spacing: 4px;
    color: var(--blue);
  }
  .back__tagline {
    position: absolute; left: 0; right: 0; top: 250px;
    text-align: center;
    color: var(--paper); font-size: 17px; letter-spacing: 0.5px;
  }
  .back__tagline .dot { margin: 0 10px; font-size: 12px; vertical-align: 2px; }

  /* Front side */
  .card--front { top: 590px; background: var(--paper); }
  .front__brand {
    position: absolute; left: 40px; top: 130px; width: 300px;
    font-family: "Montserrat", Arial, sans-serif;
    font-weight: 700; font-size: 40px; line-height: 1.1;
    color: var(--blue);
  }
  .front__rule {
    position: absolute; left: 370px; width: 2px; background: var(--blue);
  }
  .front__rule--top { top: 0; height: 60px; }
  .front__rule--bottom { bottom: 0; height: 60px; }
  .details { position: absolute; left: 360px; top: 72px; width: 320px; }
  .detail { display: flex; align-items: flex-start; margin-bottom: 18px; }
  .detail__icon { width: 22px; height: 22px; flex: none; margin-right: 18px; margin-top: 2px; }
  .detail__text { color: var(--grey-text); font-size: 18px; line-height: 1.3; }
  .person__name {
    font-family: "Montserrat", Arial, sans-serif;
    font-weight: 700; font-size: 24px; color: var(--blue); letter-spacing: 1px;
  }
  .person__role {
    font-family: "Montserrat", Arial, sans-serif;
    font-weight: 600; font-size: 17px; color: var(--grey-text); letter-spacing: 0.5px;
  }
</style>
</head>
<body>

<section class="card card--back" aria-label="Card back">
  <div class="back__brand">NORVALE</div>
  <p class="back__tagline">Providing leadership<span class="dot">●</span>delivering success</p>
</section>

<section class="card card--front" aria-label="Card front">
  <div class="front__brand">Norvale International</div>

  <span class="front__rule front__rule--top"></span>
  <span class="front__rule front__rule--bottom"></span>

  <div class="details">
    <div class="detail">
      <svg class="detail__icon" viewBox="0 0 24 24" aria-hidden="true"><circle cx="12" cy="8" r="5" fill="var(--blue)"/><path d="M3 22c0-5 4-8 9-8s9 3 9 8z" fill="var(--blue)"/></svg>
      <div>
        <div class="person__name">DANIEL REYES</div>
        <div class="person__role">CEO/FOUNDER</div>
      </div>
    </div>
    <div class="detail">
      <svg class="detail__icon" viewBox="0 0 24 24" aria-hidden="true"><path d="M12 2a7 7 0 0 0-7 7c0 5 7 13 7 13s7-8 7-13a7 7 0 0 0-7-7z" fill="var(--blue)"/><circle cx="12" cy="9" r="2.6" fill="var(--paper)"/></svg>
      <div class="detail__text">4120 Birchwood Court<br>Juneau, Alaska 99801</div>
    </div>
    <div class="detail">
      <svg class="detail__icon" viewBox="0 0 24 24" aria-hidden="true"><path d="M6.6 10.8a15 15 0 0 0 6.6 6.6l2.2-2.2a1 1 0 0 1 1-.25 11.4 11.4 0 0 0 3.6.57 1 1 0 0 1 1 1V20a1 1 0 0 1-1 1A17 17 0 0 1 3 4a1 1 0 0 1 1-1h3.5a1 1 0 0 1 1 1c0 1.25.2 2.45.57 3.6a1 1 0 0 1-.25 1z" fill="var(--blue)"/></svg>
      <div class="detail__text">555 214 0187<br>555 386 7420</div>
    </div>
    <div class="detail">
      <svg class="detail__icon" viewBox="0 0 24 24" aria-hidden="true"><circle cx="12" cy="12" r="10" fill="var(--blue)"/><path d="M2 12h20M12 2c3 3 3 17 0 20M12 2c-3 3-3 17 0 20" stroke="var(--paper)" stroke-width="1.4" fill="none"/></svg>
      <div class="detail__text">daniel@norvaleintl.com<br>www.norvaleintl.com</div>
    </div>
  </div>
</section>

</body>
</html>
```